Business cards for Harbourline Supply Pty Ltd that import building products into Australia from China
Target Market(s)
Business to Business
Industry/Entity Type
Business
Contact Information for Business Card
Front: Logo and Business Name
Rear:
Desmond Varrick
General Manager
Mobile: 0427 561 394
email: dessie@harbourlinesupply.com.au
alternative email: dessie@outbackworks.com.au
web: www.harbourlinesupply.com.au
Perth, Hobart and Cairns
Colors
ec1f27
fbee3d

```html
<!DOCTYPE html>
<html lang="en">
<head>
<meta charset="utf-8">
<title>Harbourline Supply Pty Ltd – Business Cards</title>
<link rel="stylesheet" href="https://fonts.googleapis.com/css2?family=Source+Sans+3:wght@400;600;700&display=swap">
<style>
  :root {
    --brand-red: #ec1f27;
    --brand-yellow: #fbee3d;
    --ink: #231f20;
    --paper: #ffffff;
    --backdrop: #e9e6e3;
  }
  * { box-sizing: border-box; margin: 0; padding: 0; }
  html, body {
    width: 1200px;
    height: 900px;
    overflow: hidden;
    background: var(--backdrop);
    font-family: "Source Sans 3", Arial, sans-serif;
  }
  .stage { position: relative; width: 1200px; height: 900px; }

  .card {
    position: absolute;
    background: var(--paper);
    overflow: hidden;
    box-shadow: 0 6px 18px rgba(0,0,0,0.18);
  }

  /* Contact side */
  .card--contact { left: 77px; top: 33px; width: 589px; height: 364px; }
  .card--contact .band { position: absolute; left: 0; top: 0; width: 589px; height: 364px; }
  .card--contact .company-name {
    position: absolute; left: 0; right: 0; top: 62px;
    text-align: center;
    font-size: 36px; font-weight: 700;
    color: var(--ink);
    letter-spacing: -0.3px;
  }
  .person {
    position: absolute; right: 313px; top: 267px;
    text-align: right; color: var(--paper);
    white-space: nowrap;
  }
  .person__name { font-size: 22px; font-weight: 600; line-height: 26px; letter-spacing: 0.3px; }
  .person__role, .person__cities { font-size: 16px; line-height: 22px; }
  .person__cities { margin-top: 3px; }
  .divider {
    position: absolute; left: 295px; top: 272px;
    width: 1px; height: 62px; background: var(--paper);
  }
  .contacts {
    position: absolute; left: 307px; top: 269px;
    list-style: none; color: var(--paper);
    font-size: 16px; line-height: 21.5px;
    white-space: nowrap;
  }
  .contacts li { display: flex; align-items: center; gap: 9px; }
  .contacts svg { width: 13px; height: 13px; flex: none; }

  /* Brand side */
  .card--brand { left: 388px; top: 505px; width: 567px; height: 352px; }
  .brand-square {
    position: absolute; left: 233px; top: 60px;
    width: 100px; height: 100px; background: var(--brand-red);
  }
  .card--brand .company-name {
    position: absolute; left: 0; right: 0; top: 186px;
    text-align: center;
    font-size: 36px; font-weight: 700;
    color: var(--ink);
    letter-spacing: -0.3px;
  }
  .website {
    position: absolute; left: 0; right: 0; top: 290px;
    text-align: center; font-size: 15px; color: var(--ink);
  }
  .website__domain { color: var(--brand-red); }
</style>
</head>
<body>
<main class="stage">

  <section class="card card--contact" aria-label="Contact side of business card">
    <svg class="band" viewBox="0 0 589 364" aria-hidden="true">
      <polygon points="0,199 404,199 388,227 0,227" fill="var(--brand-yellow)"/>
      <polygon points="0,229 384,229 416,192 589,192 589,364 0,364" fill="var(--brand-red)"/>
    </svg>
    <div class="company-name">Harbourline Supply Pty Ltd</div>

    <div class="person">
      <div class="person__name">DESMOND VARRICK</div>
      <div class="person__role">General Manager</div>
      <div class="person__cities">Perth, Hobart and Cairns</div>
    </div>
    <div class="divider"></div>
    <ul class="contacts">
      <li>
        <svg viewBox="0 0 13 13" aria-hidden="true"><rect x="3" y="0.5" width="7" height="12" rx="1.2" fill="none" stroke="#fff" stroke-width="1.3"/><rect x="5.5" y="10" width="2" height="1" fill="#fff"/></svg>
        0427 561 394
      </li>
      <li>
        <svg viewBox="0 0 13 13" aria-hidden="true"><rect x="0.5" y="2.5" width="12" height="8" fill="#fff"/><polyline points="0.5,2.5 6.5,7 12.5,2.5" fill="none" stroke="var(--brand-red)" stroke-width="1"/></svg>
        dessie@harbourlinesupply.com.au
      </li>
      <li>
        <svg viewBox="0 0 13 13" aria-hidden="true"><rect x="0.5" y="2.5" width="12" height="8" fill="#fff"/><polyline points="0.5,2.5 6.5,7 12.5,2.5" fill="none" stroke="var(--brand-red)" stroke-width="1"/></svg>
        dessie@outbackworks.com.au
      </li>
    </ul>
  </section>

  <section class="card card--brand" aria-label="Brand side of business card">
    <div class="brand-square" aria-hidden="true"></div>
    <div class="company-name">Harbourline Supply Pty Ltd</div>
    <div class="website">www.<span class="website__domain">harbourlinesupply</span>.com.au</div>
  </section>

</main>
</body>
</html>
```